Business Card Design & Gift cards, Gift Cert, Donation Card

Retail Gift Store-in addition to Business Cards we'd like sequenced 2 sided Gift cards, Gift Certificate Cards, and Donation Cards.please see examples and email for clarificationlogos attached with examples-
Gift Card, Gift Certificate and Donation Card will all be same style just differant upper right title, with back side info as example.
business card, as example is single sided.
looking for additional ideas for layout

Industry/Entity Type

Business

Contact Information for Business Card

211 Newman St.East Tawas, MI 48730989.362.8730Office@BrewKrew.com

Requirements
Must have
• Blue as per example
• Logos provided
• like gradiant background

```html
<!DOCTYPE html>
<html lang="en">
<head>
<meta charset="utf-8">
<title>Tillow Marsh – Gift Card &amp; Business Card</title>
<link href="https://fonts.googleapis.com/css2?family=Comic+Neue:wght@400;700&display=swap" rel="stylesheet">
<style>
  :root {
    --backdrop: #d9d2c6;
    --card-top: #ffffff;
    --card-bottom: #dcdcdc;
    --frame: #111111;
    --ink: #2b2b2b;
    --rule: #9a9a9a;
    --divider: #c8c8c8;
    --brand-blue: #1f2fbf;
  }
  * { box-sizing: border-box; margin: 0; padding: 0; }
  html, body { width: 1200px; height: 843px; overflow: hidden; }
  body {
    background: var(--backdrop);
    font-family: "Comic Neue", "Comic Sans MS", cursive;
    color: var(--ink);
    position: relative;
  }
  .card {
    position: absolute;
    width: 540px;
    height: 310px;
    border-radius: 22px;
    background: linear-gradient(160deg, var(--card-top) 35%, var(--card-bottom) 100%);
    box-shadow: 0 6px 18px rgba(0,0,0,0.25);
    overflow: hidden;
  }
  .card__frame {
    position: absolute;
    inset: 18px;
    border: 2.5px solid var(--frame);
    border-radius: 20px;
  }
  .gift-card { left: 40px; top: 266px; }
  .business-card { left: 620px; top: 266px; }

  /* gift card back */
  .gift-card__number {
    position: absolute; right: 40px; top: 28px;
    font-size: 13px;
  }
  .gift-card__field {
    position: absolute; left: 44px;
    display: flex; align-items: flex-end; gap: 10px;
    font-size: 17px;
  }
  .gift-card__field--large { font-size: 20px; font-weight: 700; }
  .gift-card__line {
    flex: 1;
    border-bottom: 1px solid var(--rule);
    height: 1px;
    margin-bottom: 5px;
  }
  .gift-card__field--to { top: 68px; width: 450px; }
  .gift-card__field--from { top: 106px; width: 450px; }
  .gift-card__field--issued { top: 168px; width: 320px; }
  .gift-card__field--expiry { top: 202px; width: 320px; }
  .gift-card__field--employee { top: 236px; width: 320px; }
  .gift-card__extra-line {
    position: absolute; left: 44px; width: 450px; top: 60px;
    border-bottom: 1px solid var(--rule);
  }
  .gift-card__brand {
    position: absolute; right: 44px; top: 178px;
    display: flex; align-items: center; gap: 8px;
    font-size: 17px; font-weight: 700; color: var(--brand-blue);
  }
  .brand-dot {
    width: 14px; height: 14px; border-radius: 50%;
    background: var(--brand-blue);
  }

  /* business card front */
  .business-card__name {
    position: absolute; left: 44px; top: 132px;
    width: 240px;
    font-size: 30px; font-weight: 400; letter-spacing: 0.5px;
    text-transform: uppercase;
    white-space: nowrap;
  }
  .business-card__divider {
    position: absolute; left: 298px; top: 60px; height: 190px;
    border-left: 1px solid var(--divider);
  }
  .business-card__details {
    position: absolute; left: 312px; top: 60px;
    font-size: 15px; line-height: 19px;
    white-space: nowrap;
  }
  .contact-row { display: flex; align-items: center; gap: 6px; }
  .contact-row svg { width: 12px; height: 12px; flex: none; }
  .services { margin-top: 4px; }
</style>
</head>
<body>

<section class="card gift-card" aria-label="Gift card back">
  <div class="card__frame"></div>
  <div class="gift-card__number">Card Number : 58724</div>
  <div class="gift-card__extra-line"></div>
  <div class="gift-card__field gift-card__field--large gift-card__field--to"><span>To :</span><span class="gift-card__line"></span></div>
  <div class="gift-card__field gift-card__field--large gift-card__field--from"><span>Form :</span><span class="gift-card__line"></span></div>
  <div class="gift-card__field gift-card__field--issued"><span>Date Issued :</span><span class="gift-card__line"></span></div>
  <div class="gift-card__field gift-card__field--expiry"><span>Expiration Date :</span><span class="gift-card__line"></span></div>
  <div class="gift-card__field gift-card__field--employee"><span>Employee :</span><span class="gift-card__line"></span></div>
  <div class="gift-card__brand"><span class="brand-dot"></span>Tillow Marsh</div>
</section>

<section class="card business-card" aria-label="Business card">
  <div class="card__frame"></div>
  <div class="business-card__name">Tillow Marsh</div>
  <div class="business-card__divider"></div>
  <div class="business-card__details">
    <div>482 Larkfield Ave.</div>
    <div>Harlow Bay, MI 48736</div>
    <div class="contact-row">
      <svg viewBox="0 0 12 12" aria-hidden="true"><path d="M2 1l2 0 1 3-1.3 1a6 6 0 0 0 3.3 3.3L8 7l3 1v2a1 1 0 0 1-1 1C5 11 1 7 1 2a1 1 0 0 1 1-1z" fill="#222"/></svg>
      <span>989.517.4296</span>
    </div>
    <div class="contact-row">
      <svg viewBox="0 0 12 12" aria-hidden="true"><rect x="0.5" y="2" width="11" height="8" rx="1" fill="#222"/><path d="M1 3l5 4 5-4" stroke="#fff" fill="none"/></svg>
      <span>Office@TillowMarsh.com</span>
    </div>
    <div class="contact-row">
      <svg viewBox="0 0 12 12" aria-hidden="true"><circle cx="6" cy="6" r="5.5" fill="#222"/><path d="M0.5 6h11M6 0.5c-3 3-3 8 0 11M6 0.5c3 3 3 8 0 11" stroke="#fff" stroke-width="0.8" fill="none"/></svg>
      <span>www.TillowMarsh.com</span>
    </div>
    <div class="services">
      <div>Gourmet Food</div>
      <div>Fine Wines | Gift Baskets</div>
      <div>Kitchen &amp; Bath Accessories</div>
      <div>Candles | Cards | Soaps</div>
    </div>
  </div>
</section>

</body>
</html>
```